Brindle Sky Port needs a new upscale business card design for our high end aircraft hangar complex

Brindle Sky Port (BSP) is a large, upscale jet hangar complex in the US housing expensive aircraft. We need a new business card design, using our current logo. We will be attending a industry convention and need a card design that will stand out and be remembered by aircraft owners and private pilots.

Target Market(s)

Aircraft pilots or owners looking for a new upscale hangar

Industry/Entity Type

Airport

Contact Information for Business Card

I like to use very heavy card stock, 400#, double sided. Square, no rounded edges please.

Colors
3276b5
0255a3
85abd2

Requirements
Must have
• An expensive, classy design, vivid colors.
Nice to have
• Needs to look very expensive and classy, and have some "pop". Designer must be able to download or copy my current typeface or fonts.
• One card side might be black with the "Logo and Brindle Sky Port Double line image in blue (or try gold, or glossy black), and perhaps have a grayed out "K720 jet silhouette". The other card side would have our contact info, and perhaps the "BSP Logo only". I'd like my contact info 'stacked', not in a paragraph format.
Should not have
• Should not look "too busy". Having a double-sided card will help.

```html
<!DOCTYPE html>
<html lang="en">
<head>
<meta charset="utf-8">
<title>Brindle Sky Port – Business Card</title>
<link href="https://fonts.googleapis.com/css2?family=Open+Sans:ital,wght@0,600;0,700;0,800;1,700;1,800&display=swap" rel="stylesheet">
<style>
  :root {
    --brand-blue: #3276b5;
    --deep-blue: #0255a3;
    --sky-blue: #85abd2;
    --card-black: #1b1b1c;
    --card-charcoal: #2e2e30;
    --panel-grey: #2a2a2c;
    --text-white: #ffffff;
    --page-white: #ffffff;
  }
  * { margin: 0; padding: 0; box-sizing: border-box; }
  html, body {
    width: 1200px; height: 334px; overflow: hidden;
    background: var(--page-white);
    font-family: "Open Sans", Arial, sans-serif;
  }
  .canvas { position: relative; width: 1200px; height: 334px; }
  .card {
    position: absolute; top: 0; height: 334px; overflow: hidden;
    background: radial-gradient(ellipse at 45% 40%, var(--card-charcoal) 0%, var(--card-black) 75%);
  }
  .card--front { left: 0; width: 592px; }
  .card--back { left: 610px; width: 590px; }

  .jet-photo {
    position: absolute; left: 8px; top: 4px; width: 208px; height: 112px;
    background: linear-gradient(160deg, rgba(120,120,124,0.10) 0%, rgba(150,150,154,0.22) 50%, rgba(120,120,124,0.06) 100%);
  }
  .front-mark {
    position: absolute; left: 243px; top: 62px;
    width: 150px; height: 150px; border-radius: 50%;
    background: var(--deep-blue);
  }
  .brand-name {
    position: absolute; left: 0; width: 636px; top: 226px;
    text-align: center; color: var(--deep-blue);
    font-weight: 800; font-size: 44px; line-height: 52px;
  }

  .back-art { position: absolute; inset: 0; }
  .back-mark {
    position: absolute; left: 106px; top: 66px;
    width: 60px; height: 60px; border-radius: 50%;
    background: var(--deep-blue);
  }
  .back-brand {
    position: absolute; left: 26px; width: 220px; top: 134px;
    text-align: center; color: var(--deep-blue);
    font-weight: 800; font-size: 25px; line-height: 32px; white-space: nowrap;
  }
  .identity {
    position: absolute; left: 300px; width: 296px; top: 124px;
    text-align: center; color: var(--text-white); font-style: italic;
  }
  .identity__name { font-size: 52px; font-weight: 800; line-height: 56px; }
  .identity__role { font-size: 19px; font-weight: 700; line-height: 22px; }

  .contacts { position: absolute; left: 212px; top: 221px; list-style: none; }
  .contacts__item {
    display: flex; align-items: center; height: 34px;
    color: var(--text-white); font-size: 21px; font-weight: 700; white-space: nowrap;
  }
  .contacts__icon { width: 18px; height: 18px; margin-right: 15px; flex: none; }
</style>
</head>
<body>
<div class="canvas">

  <section class="card card--front">
    <div class="jet-photo" role="img" aria-label="Grey photo of a private jet banking in flight"></div>
    <div class="front-mark"></div>
    <div class="brand-name">Brindle Sky Port</div>
  </section>

  <section class="card card--back">
    <svg class="back-art" width="590" height="334" viewBox="0 0 590 334">
      <polygon points="418,0 590,0 590,334 170,334" fill="var(--panel-grey)"/>
      <line x1="418" y1="0" x2="170" y2="334" stroke="#111" stroke-width="3" opacity="0.6"/>
      <polygon points="296,124 590,124 590,206 212,206" fill="var(--brand-blue)"/>
    </svg>

    <div class="back-mark"></div>
    <div class="back-brand">Brindle Sky Port</div>

    <div class="identity">
      <div class="identity__name">Name</div>
      <div class="identity__role">Designation</div>
    </div>

    <ul class="contacts">
      <li class="contacts__item">
        <svg class="contacts__icon" viewBox="0 0 18 18"><rect x="0" y="0" width="18" height="18" fill="#fff"/><rect x="5.5" y="3" width="7" height="12" rx="1.5" fill="none" stroke="#1b1b1c" stroke-width="1.6"/></svg>
        phone : +001 123-456-789
      </li>
      <li class="contacts__item">
        <svg class="contacts__icon" viewBox="0 0 18 18"><rect x="0" y="0" width="18" height="18" fill="#fff"/><rect x="3" y="5" width="12" height="8" fill="none" stroke="#1b1b1c" stroke-width="1.4"/><polyline points="3,5 9,10 15,5" fill="none" stroke="#1b1b1c" stroke-width="1.4"/></svg>
        e-mail: youremail@email.com
      </li>
      <li class="contacts__item">
        <svg class="contacts__icon" viewBox="0 0 18 18"><rect x="0" y="0" width="18" height="18" fill="#fff"/><circle cx="9" cy="9" r="6" fill="none" stroke="#1b1b1c" stroke-width="1.3"/><ellipse cx="9" cy="9" rx="2.6" ry="6" fill="none" stroke="#1b1b1c" stroke-width="1.1"/><line x1="3" y1="9" x2="15" y2="9" stroke="#1b1b1c" stroke-width="1.1"/></svg>
        website: www.yoursite.com
      </li>
    </ul>
  </section>

</div>
</body>
</html>
```